Revise our price listr for 2023

Please see attached price list with new prices to revise.
Please include new logo
Please add the text: Please note that prices are subject to change without prior notice.
Please remove prices from equipment with operator
Please add Under Commercial stone:
Fill Dirt $16.
Please add under Decorative Stone:
3/4" Barn Red Stone $127.
3/4" Yellow Ocean Gravel $140.
3/4" Delaware River Gravel $110.
1" Nutmeg Pebble $97.
Price list sending via email and customer in our lobby
Landscape and construction supply

```html
<!DOCTYPE html>
<html lang="en">
<head>
<meta charset="utf-8">
<title>Ridgeline Supply – Material Price List 2023</title>
<link href="https://fonts.googleapis.com/css2?family=Poppins:wght@400;500;600;700;800&display=swap" rel="stylesheet">
<style>
  :root{
    --green:#12984a;
    --maroon:#7a1b1d;
    --orange:#ee971a;
    --ink:#1b1b1b;
    --card:#f6f6f4;
    --paper:#ffffff;
    --stone-light:#d9ccb3;
    --stone-mid:#a39380;
    --stone-dark:#5f5446;
  }
  *{box-sizing:border-box;margin:0;padding:0}
  html,body{width:1200px;height:800px;overflow:hidden;background:#efece6}
  body{font-family:"Poppins",sans-serif;color:var(--ink)}
  .flyer{position:relative;width:1200px;height:800px;background:var(--paper);overflow:hidden}
  .accent{position:absolute;background:var(--orange)}
  .accent--top{left:0;top:0;width:310px;height:32px}
  .accent--left{left:0;top:0;width:35px;height:585px}
  .accent--right{right:0;top:432px;width:25px;height:368px}
  .accent--bottom{left:889px;bottom:0;width:311px;height:34px}
  .stage{position:absolute;left:35px;top:32px;width:1140px;height:734px;background:var(--paper)}
  .photo{position:absolute;left:0;top:0;width:100%;height:100%;
    background:
      linear-gradient(180deg,#fff 0%,#fff 12%,rgba(255,255,255,0) 27%),
      linear-gradient(105deg,var(--stone-light) 0%,var(--stone-light) 33%,var(--stone-mid) 52%,var(--stone-dark) 78%,#4d4438 100%)}
  .brand{position:absolute;left:70px;top:68px;display:flex;align-items:center;gap:12px}
  .brand__dot{width:44px;height:44px;border-radius:50%;background:var(--maroon)}
  .brand__name{font-weight:800;font-size:40px;color:var(--maroon);letter-spacing:.5px;line-height:1}
  .title{position:absolute;right:72px;top:50px;text-align:right;font-weight:800;line-height:1}
  .title__top{font-size:58px;color:var(--ink);letter-spacing:1px}
  .title__bottom{font-size:58px;margin-top:4px}
  .title__green{color:var(--green)}
  .card{position:absolute;background:var(--card);border-radius:14px;overflow:hidden;font-size:11.5px;font-weight:600}
  .card__head{height:26px;color:#fff;font-weight:700;font-size:15px;letter-spacing:.5px;padding:3px 0 0 22px;
    clip-path:polygon(0 0,100% 0,82% 100%,0 100%);width:62%}
  .card__head--green{background:var(--green)}
  .card__head--maroon{background:var(--maroon)}
  .rows{list-style:none;padding:4px 20px 0 22px}
  .rows li{display:flex;justify-content:space-between;height:20.5px;align-items:center}
  .note{font-size:7px;color:var(--maroon);font-weight:600;margin:-5px 0 4px 24px}
  .equip{left:676px;top:190px;width:461px;height:318px;font-size:11.5px}
  .equip .card__head{height:50px;width:73%;font-size:14.5px;line-height:19px;padding:6px 0 0 12px;clip-path:polygon(0 0,100% 0,88% 100%,0 100%)}
  .e{position:absolute;line-height:16px}
  .e b{font-weight:700}
  .e span{font-weight:500}
  .e small{display:block;font-size:7.5px;line-height:9px;font-weight:500}
  .rule{position:absolute;background:var(--ink)}
  .dyk{position:absolute;left:700px;top:530px;width:440px;height:200px;color:#fff}
  .dyk__you{position:absolute;left:80px;top:12px;background:#111;font-weight:800;font-size:34px;line-height:42px;padding:0 6px}
  .dyk__know{position:absolute;left:86px;top:54px;background:var(--orange);font-weight:800;font-size:30px;line-height:34px;padding:0 10px}
  .dyk__bulb{position:absolute;left:275px;top:-6px}
  .dyk__text{position:absolute;left:0;top:108px;width:440px;text-align:center;font-size:19px;line-height:23px;font-weight:400}
  .dyk__text b{font-weight:700}
  .notice{position:absolute;left:698px;top:743px;width:465px;height:23px;background:var(--maroon);color:#fff;font-size:10px;
    padding:5px 0 0 36px;clip-path:polygon(6% 0,100% 0,100% 100%,0 100%)}
  .notice b{font-weight:700}
</style>
</head>
<body>
<main class="flyer">
  <div class="accent accent--top"></div>
  <div class="accent accent--left"></div>
  <div class="accent accent--right"></div>
  <div class="accent accent--bottom"></div>
  <div class="stage">
    <div class="photo" role="img" aria-label="Background photograph of landscaping river stones and gravel"></div>
  </div>

  <div class="brand"><div class="brand__dot"></div><div class="brand__name">RIDGELINE SUPPLY</div></div>

  <h1 class="title">
    <div class="title__top">MATERIAL</div>
    <div class="title__bottom"><span class="title__green">PRICE LIST</span> 2023</div>
  </h1>

  <section class="card" style="left:65px;top:190px;width:280px;height:128px">
    <div class="card__head card__head--green">SOIL</div>
    <ul class="rows">
      <li><span>Sandy Loam</span><span>$30</span></li>
      <li><span>Topsoil-screened</span><span>$42</span></li>
      <li><span>Garden Soil</span><span>$52</span></li>
      <li><span>Mushroom Dirt</span><span>$55</span></li>
      <li><span>Compost (leaf &amp; Grass)</span><span>$55</span></li>
    </ul>
  </section>

  <section class="card" style="left:65px;top:328px;width:280px;height:152px">
    <div class="card__head card__head--maroon">MULCH</div>
    <ul class="rows" style="padding-top:8px">
      <li><span>Mulch-Dyed Black</span><span>$42</span></li>
      <li><span>Mulch-Dyedred</span><span>$42</span></li>
      <li><span>Mulch-Dyed Brown</span><span>$42</span></li>
      <li><span>Mulch-Dyed Light Brown</span><span>$38</span></li>
      <li><span>Mulch-Dark Triple Ground</span><span>$44</span></li>
      <li><span>Mulch Cedar</span><span>$55</span></li>
    </ul>
  </section>

  <section class="card" style="left:70px;top:491px;width:280px;height:261px">
    <div class="card__head card__head--green" style="width:86%;padding-left:10px">DECORATIVE STONE</div>
    <ul class="rows" style="padding-top:8px;padding-right:14px">
      <li><span>White Limestone#1 (1/4"-1/2")</span><span>$95</span></li>
      <li><span>White Limestone #2 (1/2"-3/4")</span><span>$97.50</span></li>
      <li><span>River Rock #2(3/4") Round</span><span>$50</span></li>
      <li><span>River Rock-medium ( 2/3")</span><span>$95</span></li>
      <li><span>River Rounds(4-6")</span><span>$90</span></li>
      <li><span>Pea Gravel</span><span>$50</span></li>
      <li><span>Bershire Blend</span><span>$120</span></li>
      <li><span>Barn Red Stone (3/4")</span><span>$127</span></li>
      <li><span>Yellow Ocean Gravel (3/4")</span><span>$140</span></li>
      <li><span>Delaware River Gravel (3/4")</span><span>$110</span></li>
      <li><span>Nutmeg Pebble (1")</span><span>$97</span></li>
    </ul>
  </section>

  <section class="card" style="left:371px;top:190px;width:279px;height:91px">
    <div class="card__head card__head--maroon">SAND</div>
    <ul class="rows" style="padding-top:12px">
      <li><span>Masonary / Pool Sand</span><span>$45</span></li>
      <li><span>Bedding Sand</span><span>$37</span></li>
    </ul>
  </section>

  <section class="card" style="left:371px;top:288px;width:279px;height:232px">
    <div class="card__head card__head--green" style="width:92%;padding-left:14px">COMMERCIAL STONE</div>
    <ul class="rows" style="padding-left:14px;padding-right:14px">
      <li><span>Item #4</span><span>$42</span></li>
      <li><span>#1 Stone (1/2")</span><span>$45</span></li>
      <li><span>#2 Stone (3/4"1)</span><span>$45</span></li>
      <li><span>#3 (1.5"2)</span><span>$45</span></li>
      <li><span>Stone Chip (Fine)</span><span>$40</span></li>
      <li><span>Stone Dust (Extra Fine)</span><span>$47</span></li>
      <li><span>Shake When Available</span><span>CALL</span></li>
      <li><span>Bank Run Fill (Dirt &amp; Cobble)</span><span>$18</span></li>
      <li><span>Crusher Run</span><span>$42</span></li>
      <li><span>Fill Dirt</span><span>$16</span></li>
    </ul>
  </section>

  <section class="card" style="left:371px;top:531px;width:279px;height:123px">
    <div class="card__head card__head--maroon" style="width:88%">DELIVERY CHARGES</div>
    <ul class="rows" style="padding-left:14px;padding-right:14px;padding-top:6px">
      <li><span>Local (Small Truck)</span><span>$60</span></li>
      <li><span>Local (Medium Truck)</span><span>$75</span></li>
      <li><span>Local (Large Truck)</span><span>$115</span></li>
    </ul>
    <p class="note">Local delivery 7 mile Radius excluding the mt.</p>
    <ul class="rows" style="padding-left:14px;padding-right:14px;padding-top:0">
      <li><span>Non Local</span><span>CALL</span></li>
    </ul>
  </section>

  <section class="card" style="left:371px;top:663px;width:279px;height:63px">
    <div class="card__head card__head--green" style="width:52%;padding-left:14px">SEASONAL</div>
    <ul class="rows" style="padding-left:14px;padding-right:28px;padding-top:8px">
      <li><span>Reated Salt Green</span><span>$16</span></li>
    </ul>
  </section>

  <section class="card equip">
    <div class="card__head card__head--maroon">EQUIPMENT WITH OPERATOR<br>AVAILABLE CALL FOR PRICING</div>
    <div class="e" style="left:20px;top:70px;width:140px;line-height:14px"><b>ONSITE MOBILE GRINDING / TUBE GRINDING</b></div>
    <div class="e" style="left:20px;top:114px"><b>FORESTRY MULCHING</b></div>
    <div class="e" style="left:20px;top:142px"><b>EXCAVATOR :</b><br><span>35 Class (7,500lbs)<br>60 Class (14,000 Bs)<br>140 Class (45,500lbs)<br>160 Class (38.500bs)<br>250 Class (60,000bs)</span></div>
    <div class="e" style="left:20px;top:252px;width:140px"><b>ROCK HAMMER</b><small>Hydraulic Rock Hammer on 160 class excavator additional Mobilization FREE for 1st day</small></div>
    <div class="rule" style="left:168px;top:62px;width:1.5px;height:84px"></div>
    <div class="rule" style="left:171px;top:150px;width:1.5px;height:86px"></div>
    <div class="rule" style="left:171px;top:250px;width:1.5px;height:50px"></div>
    <div class="e" style="left:188px;top:72px"><b>SKID STEER : (RUBBER TRACK)</b></div>
    <div class="e" style="left:190px;top:89px;line-height:17px"><span>Available Attachment<br>Harlan Rake<br>Forestry Mulching</span></div>
    <div class="rule" style="left:272px;top:113px;width:50px;height:1px"></div>
    <div class="rule" style="left:298px;top:135px;width:32px;height:1px"></div>
    <div class="e" style="left:338px;top:106px;line-height:16px"><span>3/4 Yard Bucket</span></div>
    <div class="e" style="left:338px;top:128px;line-height:15px"><span>Hydraulic Auger<br>Grapple Bucket</span></div>
    <div class="e" style="left:188px;top:154px"><b>BULL DOZER :</b><br><span>450 Class (18,000bs)<br>700 Class (30,000bs)</span></div>
    <div class="e" style="left:188px;top:216px"><b>VIBRATORY ROLLER</b></div>
    <div class="rule" style="left:188px;top:240px;width:118px;height:1.5px"></div>
    <div class="e" style="left:190px;top:258px"><b>TRI-AXLE DUMP</b></div>
    <div class="e" style="left:190px;top:278px"><b>DUMP TRAILER</b></div>
    <div class="rule" style="left:300px;top:267px;width:102px;height:1px"></div>
    <div class="rule" style="left:290px;top:287px;width:110px;height:1px"></div>
    <div class="e" style="left:410px;top:259px"><b>CALL</b></div>
    <div class="e" style="left:410px;top:279px"><b>CALL</b></div>
  </section>

  <section class="dyk">
    <div class="dyk__you">DID YOU</div>
    <div class="dyk__know">KNOW?</div>
    <svg class="dyk__bulb" width="80" height="80" viewBox="0 0 80 80" aria-hidden="true">
      <g fill="none" stroke="#111" stroke-width="4" stroke-linecap="round">
        <circle cx="36" cy="34" r="20" fill="#fff"/>
        <path d="M28 54 L30 66 L42 66 L44 54" fill="#fff"/>
        <path d="M30 60 L43 60"/>
      </g>
      <g stroke="var(--orange)" stroke-width="3.5" stroke-linecap="round">
        <path d="M36 4 V9"/><path d="M62 12 L58 16"/><path d="M70 34 H65"/><path d="M10 12 L14 16"/><path d="M2 34 H7"/>
      </g>
    </svg>
    <p class="dyk__text">We offer <b>onside Tube Grinding</b> &amp;<br>We are <b>Green Recycling Location !</b><br>Non local call for pricing also thank you</p>
  </section>

  <p class="notice"><b>Please note</b> that prices are subject to change without prior notice.</p>
</main>
</body>
</html>
```